Request for Business Card Design

Hi. My name is Marlene, I am looking for a new business card design for my company, Quarrow Signal Instruments, LLC. I really like the design you did for Tarsel Venture and was hoping you could do something similar using our full logo and our mark. I am also open to any raised texture design using our mark. I have attached our full logo, which would need to be somewhere on the card, as well as the mark in both outline and full form, as well as our brand colors / guide. The card does not have to be white, as long as our logo and mark appear. I actually like darker colored business cards more, but am open to all options. If you are interested in working with me, please let me know. We would also take the business card design into letterhead design if you can do that.

```html
<!DOCTYPE html>
<html lang="en">
<head>
<meta charset="utf-8">
<title>Quarrow Signal Instruments – Business Card</title>
<link rel="stylesheet" href="https://fonts.googleapis.com/css2?family=Montserrat:wght@400;500;700&display=swap">
<style>
  :root {
    --bg: #3e3834;
    --card: #1b1b1c;
    --accent: #1a94c4;
    --mark-tint: #2c3e47;
    --text: #f2f2f2;
    --muted: #d6d6d6;
  }
  * { box-sizing: border-box; margin: 0; padding: 0; }
  html, body { width: 1200px; height: 786px; overflow: hidden; }
  body {
    background: var(--bg);
    font-family: "Montserrat", sans-serif;
    position: relative;
  }
  .card {
    position: absolute;
    top: 238px;
    width: 540px;
    height: 310px;
    background: var(--card);
    overflow: hidden;
    box-shadow: 0 10px 24px rgba(0,0,0,.45);
  }
  .card--front { left: 40px; }
  .card--back { left: 620px; }

  .brand {
    position: absolute;
    display: flex;
    align-items: center;
    gap: 10px;
  }
  .brand__dot {
    width: 30px; height: 30px;
    border-radius: 50%;
    background: var(--accent);
    flex: none;
  }
  .brand__name {
    color: var(--text);
    font-weight: 700;
    font-size: 13px;
    letter-spacing: 1.5px;
    line-height: 1.2;
    text-transform: uppercase;
    white-space: nowrap;
  }
  .card--front .brand { left: 26px; top: 168px; }

  .divider {
    position: absolute;
    left: 290px; top: 78px;
    width: 2px; height: 154px;
    background: var(--accent);
  }
  .contact {
    position: absolute;
    left: 312px; top: 82px;
    color: var(--muted);
    font-size: 12.5px;
    line-height: 1.45;
  }
  .contact__name {
    color: var(--accent);
    font-weight: 700;
    font-size: 22px;
    line-height: 1.1;
  }
  .contact__role { margin-bottom: 8px; }
  .contact__row { display: flex; align-items: center; gap: 9px; }
  .contact__row svg { width: 11px; height: 11px; fill: var(--accent); flex: none; }
  .contact__address { margin-top: 10px; }

  .card--back .decor {
    position: absolute;
    left: -60px; top: -40px;
    width: 380px; height: 380px;
    border-radius: 50%;
    background: var(--mark-tint);
  }
  .card--back .brand { right: 26px; top: 134px; }
  .card--back .brand__dot { width: 28px; height: 28px; }
</style>
</head>
<body>

<section class="card card--front" aria-label="Business card front">
  <div class="brand">
    <span class="brand__dot"></span>
    <span class="brand__name">Quarrow<br>Signal Instruments</span>
  </div>
  <div class="divider"></div>
  <div class="contact">
    <p class="contact__name">Elias Brandt</p>
    <p class="contact__role">Owner</p>
    <p class="contact__row">
      <svg viewBox="0 0 24 24"><path d="M6.6 10.8a15.1 15.1 0 0 0 6.6 6.6l2.2-2.2a1 1 0 0 1 1-.25 11.4 11.4 0 0 0 3.6.57 1 1 0 0 1 1 1V20a1 1 0 0 1-1 1A17 17 0 0 1 3 4a1 1 0 0 1 1-1h3.5a1 1 0 0 1 1 1c0 1.25.2 2.45.57 3.57a1 1 0 0 1-.25 1z"/></svg>
      +001 555 010 2841
    </p>
    <p class="contact__row">
      <svg viewBox="0 0 24 24"><path fill-rule="evenodd" d="M2 5h20v14H2zM4 8.2V17h16V8.2l-8 5z"/></svg>
      info@quarrowsignal.com
    </p>
    <p class="contact__row">
      <svg viewBox="0 0 24 24"><circle cx="12" cy="12" r="10"/></svg>
      www.quarrowsignal.com
    </p>
    <p class="contact__address">1180 Ridgeway Court<br>Fairholt, CO 80999</p>
  </div>
</section>

<section class="card card--back" aria-label="Business card back">
  <div class="decor"></div>
  <div class="brand">
    <span class="brand__dot"></span>
    <span class="brand__name">Quarrow<br>Signal Instruments</span>
  </div>
</section>

</body>
</html>
```